Task Scheduling Web App

I have a basic web app that I need designed. It must be mobile-first but it needs to be responsive for desktop users as well.
1. Before beginning the exercise, the user inputs basic info on their country and age.
2. The user is then presented with two piles of cards (TASK or DAY), with the top card face up. They have 20 seconds before their combination is set, during which they can replace either of the cards at random as many times as they like. At any time they find a combination they’re happy with, they can progress to the next screen. If the clock runs out the combination is set based on whatever cards are showing at the time and they’re moved on to the next screen.
3. The user is presented with a blank graph; x axis is ‘How important is it?’, y axis is ‘How often does it need to be done?’. The two cards they picked in the previous screen are combined to create a COMBO and the user must place a mark somewhere on the graph to represent how important they believe the scheduled task to be vs how often it will need to be done.
4. Once the user has picked a spot on the graph, options appear for them to re-do the exercise by choosing a new combo or to progress and see how their peers are organising their tasks.
5. If they choose to view insights, they must login with Kinnexa so a popup will appear to facilitate this.
6. After logging in with Kinnexa, users can view the top 10 combinations for their demographic listed and mapped on a graph. This information is based on the selection and ranking of combinations by other users.

```html
<!DOCTYPE html>
<html lang="en">
<head>
<meta charset="utf-8">
<title>Your App – Prioritize Your Combo</title>
<link rel="stylesheet" href="https://fonts.googleapis.com/css2?family=Signika:wght@400;600;700&display=swap">
<style>
  :root {
    --page-bg: #f2f2f2;
    --status-bg: #3b3b3b;
    --green: #72d193;
    --green-dark: #4fb574;
    --green-deep: #3f9e62;
    --back-fill: #5fc383;
    --back-edge: #45a866;
    --body-top: #ebdfc2;
    --body-bottom: #e9c7aa;
    --panel: #f5f2e9;
    --ink: #333333;
    --ink-soft: #5c5c5c;
    --accent-red: #ef7a6b;
    --card-grey: #707070;
    --card-edge: #565656;
    --button-bg: #dddbd3;
    --button-text: #8e8e8e;
    --white: #ffffff;
  }
  * { box-sizing: border-box; margin: 0; padding: 0; }
  html, body { width: 1014px; height: 1200px; overflow: hidden; background: var(--page-bg); }
  body { font-family: "Signika", sans-serif; position: relative; }

  .app-screen {
    position: absolute; left: 181px; top: 20px;
    width: 483px; height: 860px;
    transform: scale(1.35); transform-origin: top left;
    background: linear-gradient(180deg, var(--body-top) 0%, #ece0cd 55%, var(--body-bottom) 100%);
    overflow: hidden;
  }

  .status-bar {
    position: absolute; left: 0; top: 0; width: 100%; height: 30px;
    background: var(--status-bg); color: var(--white);
    font-size: 19px; font-weight: 600; text-align: center; line-height: 30px;
  }
  .status-bar svg { position: absolute; top: 8px; }
  .status-signal { left: 8px; }
  .status-battery { right: 6px; }

  .nav-bar {
    position: absolute; left: 0; top: 30px; width: 100%; height: 70px;
    background: linear-gradient(180deg, #7fd89e, var(--green));
    border-bottom: 2px solid var(--green-dark);
  }
  .nav-back {
    position: absolute; left: 12px; top: 12px; width: 78px; height: 46px;
  }
  .nav-back-shape { position: absolute; left: 0; top: 0; }
  .nav-back-label {
    position: absolute; left: 19px; top: 0; line-height: 46px;
    color: var(--white); font-size: 20px; font-weight: 600;
  }
  .nav-title {
    position: absolute; left: 0; right: 0; top: 0; text-align: center;
    color: var(--white); font-size: 30px; font-weight: 600; line-height: 68px;
  }
  .nav-settings {
    position: absolute; right: 12px; top: 14px; width: 42px; height: 42px;
    background: var(--green-dark); border: 2px solid var(--green-deep); border-radius: 5px;
  }

  .step-panel {
    position: absolute; left: 40px; top: 155px; width: 403px; height: 652px;
    background: var(--panel); box-shadow: 0 0 3px rgba(0,0,0,0.08);
  }
  .step-label {
    position: absolute; top: 24px; width: 100%; text-align: center;
    font-size: 14px; font-weight: 600; color: var(--ink-soft);
  }
  .step-slider { position: absolute; left: 27px; top: 52px; }
  .step-heading {
    position: absolute; top: 100px; width: 100%; text-align: center;
    font-size: 27px; font-weight: 700; color: var(--ink); letter-spacing: 0.5px;
  }
  .step-hint {
    position: absolute; top: 136px; width: 100%; text-align: center;
    font-size: 12px; color: var(--ink-soft);
  }
  .priority-graph { position: absolute; left: 17px; top: 161px; width: 367px; height: 164px; background: var(--white); }

  .combo-tab {
    position: absolute; left: 109px; top: 341px; width: 193px; height: 40px;
    background: var(--green); border-radius: 6px 6px 0 0;
    color: var(--white); font-size: 16px; font-weight: 600; text-align: center; line-height: 40px;
  }
  .combo-card {
    position: absolute; top: 379px; width: 178px; height: 131px;
    background: var(--card-grey); border: 2px solid var(--card-edge); border-radius: 7px;
    color: var(--white); display: flex; align-items: center; justify-content: center; text-align: center;
    font-weight: 600;
  }
  .combo-task { left: 19px; font-size: 22px; line-height: 24px; }
  .combo-day { left: 207px; font-size: 32px; }
  .combo-plus { position: absolute; left: 190px; top: 433px; }

  .next-button {
    position: absolute; left: 26px; top: 560px; width: 344px; height: 50px;
    background: var(--button-bg); border: 2px solid #cfcdc5; border-radius: 5px;
    color: var(--button-text); font-size: 23px; font-weight: 600; text-align: center; line-height: 46px;
  }
</style>
</head>
<body>
<main class="app-screen">
  <header class="status-bar">
    <svg class="status-signal" width="30" height="14" viewBox="0 0 30 14" fill="#fff">
      <rect x="0" y="11" width="3" height="3"/><rect x="5" y="9" width="3" height="5"/><rect x="10" y="6" width="3" height="8"/><rect x="15" y="3" width="3" height="11"/><rect x="20" y="0" width="3" height="14"/>
    </svg>
    4:20 PM
    <svg class="status-battery" width="32" height="14" viewBox="0 0 32 14">
      <rect x="1" y="1" width="27" height="12" rx="2" fill="none" stroke="#fff" stroke-width="2"/>
      <rect x="4" y="4" width="10" height="6" fill="#fff"/><rect x="29" y="4" width="3" height="6" fill="#fff"/>
    </svg>
  </header>

  <nav class="nav-bar">
    <div class="nav-back">
      <svg class="nav-back-shape" width="78" height="46" viewBox="0 0 78 46"><path d="M2 23 L15 2 H73 a4 4 0 0 1 4 4 V40 a4 4 0 0 1 -4 4 H15 Z" fill="#5fc383" stroke="#45a866" stroke-width="2"/></svg>
      <span class="nav-back-label">Back</span>
    </div>
    <div class="nav-title">Your App</div>
    <div class="nav-settings">
      <svg width="38" height="38" viewBox="0 0 38 38">
        <g fill="#fff" transform="translate(19 19)">
          <circle r="7"/>
          <rect x="-2.5" y="-10" width="5" height="20"/><rect x="-10" y="-2.5" width="20" height="5"/>
          <rect x="-2.5" y="-10" width="5" height="20" transform="rotate(45)"/><rect x="-2.5" y="-10" width="5" height="20" transform="rotate(-45)"/>
        </g>
        <circle cx="19" cy="19" r="3" fill="#4fb574"/>
      </svg>
    </div>
  </nav>

  <section class="step-panel">
    <p class="step-label">STEP 3 OF 6</p>
    <svg class="step-slider" width="340" height="36" viewBox="0 0 340 36">
      <rect x="0" y="12" width="336" height="9" rx="4.5" fill="#d6d3c8"/>
      <rect x="0" y="12" width="160" height="9" rx="4.5" fill="#6fcc8d"/>
      <circle cx="159" cy="16.5" r="16" fill="#d9d9d9" stroke="#a9a9a9"/>
      <circle cx="159" cy="16.5" r="11" fill="#ececec"/>
    </svg>
    <h1 class="step-heading">PRIORITIZE YOUR COMBO</h1>
    <p class="step-hint">Mark on the graph below to state the importance of the combo.</p>

    <svg class="priority-graph" viewBox="0 0 367 164" font-family="Signika, sans-serif">
      <line x1="50" y1="12" x2="50" y2="138" stroke="#ef7a6b" stroke-width="3"/>
      <line x1="48" y1="137" x2="338" y2="137" stroke="#ef7a6b" stroke-width="3"/>
      <rect x="34" y="22" width="14" height="110" rx="2" fill="#ef7a6b"/>
      <text transform="translate(44 128) rotate(-90)" font-size="8" font-weight="700" fill="#fff">HOW IMPORTANT IS IT?</text>
      <text x="12" y="18" font-size="9" fill="#ef7a6b">Huge</text>
      <text x="12" y="140" font-size="9" fill="#ef7a6b">None</text>
      <rect x="94" y="140" width="194" height="16" rx="2" fill="#ef7a6b"/>
      <text x="191" y="151" font-size="8" font-weight="700" fill="#fff" text-anchor="middle">HOW OFTEN DOES IT NEED TO BE DONE?</text>
      <text x="42" y="154" font-size="9" fill="#ef7a6b">1x</text>
      <text x="333" y="154" font-size="9" fill="#ef7a6b">10x</text>
    </svg>

    <div class="combo-tab">CHOSEN COMBO</div>
    <div class="combo-card combo-task">Completing<br>office work</div>
    <div class="combo-card combo-day">Monday</div>
    <svg class="combo-plus" width="24" height="24" viewBox="0 0 24 24">
      <circle cx="12" cy="12" r="11" fill="#72d193" stroke="#4fb574"/>
      <rect x="10.5" y="6" width="3" height="12" fill="#fff"/><rect x="6" y="10.5" width="12" height="3" fill="#fff"/>
    </svg>

    <div class="next-button">Complete first to click next</div>
  </section>
</main>
</body>
</html>
```